Business Card Design Project

I require a business card with the following information on them for various different people;
name
m:
f:
e:
I have a logo already and will attached that. We are in the construction industry. I require something clean and simple but eye catching at the same time. You can use another colour with our logo if you like and you can style the logo as well if you wish. I am open.
Also it needs to be front and back design.
Industry/Entity Type
Construction
Requirements
Must have
- Logo, name, mobile, fax and email address.
Front and back design

```html
<!DOCTYPE html>
<html lang="en">
<head>
<meta charset="utf-8">
<title>Stonebridge Builders – Business Card</title>
<link href="https://fonts.googleapis.com/css2?family=Open+Sans:wght@400;700&family=Questrial&display=swap" rel="stylesheet">
<style>
  :root {
    --backdrop: #ececea;
    --card: #ffffff;
    --green-dark: #3f8f2a;
    --green-mid: #62ad3c;
    --green-light: #c9e66a;
    --brand-green: #5aaa3a;
    --ink: #555555;
    --ink-strong: #4a4a4a;
    --rule: #1c1c1c;
  }
  * { box-sizing: border-box; margin: 0; padding: 0; }
  html, body { width: 1200px; height: 407px; overflow: hidden; }
  body {
    background: var(--backdrop);
    position: relative;
    font-family: "Open Sans", Arial, sans-serif;
  }
  .card {
    position: absolute;
    top: 60px;
    width: 504px;
    height: 288px;
    background: var(--card);
    box-shadow: 0 3px 8px rgba(0,0,0,0.25);
    overflow: hidden;
  }
  .card--front { left: 58px; }
  .card--back { left: 638px; }
  .corner { position: absolute; width: 504px; height: 288px; top: 0; left: 0; }
  .brand {
    position: absolute;
    display: flex;
    align-items: center;
    gap: 10px;
    height: 40px;
    font-family: "Questrial", Arial, sans-serif;
    color: var(--brand-green);
    white-space: nowrap;
  }
  .brand__mark {
    width: 30px; height: 30px;
    background: var(--brand-green);
    border-radius: 3px;
  }
  .brand__name { font-size: 30px; line-height: 40px; letter-spacing: 0.3px; }
  .card--front .brand { left: 110px; top: 58px; }
  .card--back .brand { left: 92px; top: 122px; }
  .holder {
    position: absolute;
    left: 88px;
    top: 200px;
    color: var(--ink-strong);
  }
  .holder__name { font-size: 16px; font-weight: 700; }
  .holder__title { font-size: 13px; font-weight: 400; color: var(--ink); }
  .contacts {
    position: absolute;
    left: 88px;
    top: 234px;
    display: flex;
    gap: 14px;
    font-size: 12.5px;
    color: var(--ink);
    white-space: nowrap;
  }
</style>
</head>
<body>

<section class="card card--front">
  <svg class="corner" viewBox="0 0 504 288" aria-hidden="true">
    <defs>
      <radialGradient id="glowFront" cx="45" cy="40" r="150" gradientUnits="userSpaceOnUse">
        <stop offset="0" stop-color="var(--green-light)"/>
        <stop offset="0.55" stop-color="var(--green-mid)"/>
        <stop offset="1" stop-color="var(--green-dark)"/>
      </radialGradient>
    </defs>
    <polygon points="0,0 156,0 0,159" fill="url(#glowFront)"/>
    <line x1="166" y1="0" x2="0" y2="169" stroke="var(--rule)" stroke-width="2"/>
  </svg>
  <div class="brand">
    <span class="brand__mark"></span>
    <span class="brand__name">Stonebridge Builders</span>
  </div>
  <p class="holder">
    <span class="holder__name">Your Name</span>
    <span class="holder__title"> / Title</span>
  </p>
  <p class="contacts">
    <span>C : 123-456-7890</span>
    <span>F : 123-456-7890</span>
    <span>E : name@website.com</span>
  </p>
</section>

<section class="card card--back">
  <svg class="corner" viewBox="0 0 504 288" aria-hidden="true">
    <defs>
      <radialGradient id="glowBack" cx="460" cy="245" r="150" gradientUnits="userSpaceOnUse">
        <stop offset="0" stop-color="var(--green-light)"/>
        <stop offset="0.55" stop-color="var(--green-mid)"/>
        <stop offset="1" stop-color="var(--green-dark)"/>
      </radialGradient>
    </defs>
    <polygon points="504,128 504,288 348,288" fill="url(#glowBack)"/>
    <line x1="504" y1="118" x2="338" y2="288" stroke="var(--rule)" stroke-width="2"/>
  </svg>
  <div class="brand">
    <span class="brand__mark"></span>
    <span class="brand__name">Stonebridge Builders</span>
  </div>
</section>

</body>
</html>
```